Mobile welding fabrication and repair, heavy equipment and semi repair

We need a business card design that will catch the eye but look prelesional at the same time. Were based out of Idaho and we do all welding fabrication jobs and repairs, we also build and install custom pipe fences for personal or larger scale fence jobs and can give free quotes. We can do semi truck and trailer repairs Mobily also.

Target Market(s)

Welding

Industry/Entity Type

welding and repair

Contact Information for Business Card

email (ravenforgeandmend@mailbay.net, phone number 208-417-3826, owner (Dalton Whitcomb), Pipe Fence, Semi Repair, Mobile welding and fabrication

Font styles to use
Sans Serif

Requirements
Must have
• My logo in black background on one side , and other side my logo in white back round with all the information listed on card details
Nice to have
• make it stand out from other business cards

```html
<!DOCTYPE html>
<html lang="en">
<head>
<meta charset="UTF-8">
<title>Raven Forge and Mend – Business Card</title>
<link href="https://fonts.googleapis.com/css2?family=Lato:wght@400;700;900&display=swap" rel="stylesheet">
<style>
  :root {
    --bg: #2a2a2c;
    --blue-light: #0b98d6;
    --blue-mid: #0a78c8;
    --blue-deep: #0750b0;
    --white: #ffffff;
    --ink: #1f1f22;
  }
  * { margin: 0; padding: 0; box-sizing: border-box; }
  html, body {
    width: 1200px; height: 1015px; overflow: hidden;
    background: var(--bg);
    font-family: "Lato", Arial, sans-serif;
  }
  .canvas {
    position: relative; width: 1200px; height: 1015px;
    display: flex; flex-direction: column; align-items: center; justify-content: center; gap: 44px;
  }
  .card {
    position: relative; width: 760px; height: 434px; overflow: hidden;
    border-radius: 4px;
    box-shadow: 0 18px 40px rgba(0,0,0,.55);
  }
  .card-front {
    background: linear-gradient(160deg, var(--blue-light) 0%, var(--blue-mid) 45%, var(--blue-deep) 100%);
    display: flex; align-items: center; justify-content: center;
  }
  .brand {
    display: flex; align-items: center; gap: 16px;
    font-weight: 900; letter-spacing: 2px; text-transform: uppercase;
  }
  .brand-dot { width: 22px; height: 22px; border-radius: 50%; flex: none; }
  .card-front .brand { color: var(--white); font-size: 44px; }
  .card-front .brand-dot { background: var(--white); }

  .card-back {
    background: linear-gradient(165deg, var(--blue-light) 0%, var(--blue-mid) 50%, var(--blue-deep) 100%);
    color: var(--white);
  }
  .back-shape { position: absolute; inset: 0; }
  .card-back .brand {
    position: absolute; left: 490px; top: 172px; width: 250px;
    color: var(--blue-mid); font-size: 27px; letter-spacing: 1px; line-height: 1.1; gap: 10px;
  }
  .card-back .brand-dot { background: var(--blue-mid); width: 14px; height: 14px; }
  .owner { position: absolute; left: 46px; top: 84px; }
  .owner-name { font-size: 30px; font-weight: 700; letter-spacing: .5px; text-transform: uppercase; }
  .owner-role { font-size: 21px; font-weight: 400; letter-spacing: 1px; margin-left: 14px; text-transform: uppercase; }
  .services { position: absolute; left: 74px; top: 196px; list-style: none; }
  .services li {
    font-size: 17px; letter-spacing: .5px; text-transform: uppercase; line-height: 25px;
    display: flex; align-items: center; gap: 14px;
  }
  .services li::before {
    content: ""; width: 10px; height: 10px; border-radius: 50%; background: var(--white);
  }
  .contact { position: absolute; left: 126px; top: 340px; }
  .contact-row { display: flex; align-items: center; gap: 10px; font-size: 20px; line-height: 30px; }
  .contact-row svg { width: 20px; height: 20px; flex: none; }
</style>
</head>
<body>
<main class="canvas">
  <section class="card card-front" aria-label="Card front">
    <div class="brand"><span class="brand-dot"></span>Raven Forge and Mend</div>
  </section>

  <section class="card card-back" aria-label="Card back">
    <svg class="back-shape" viewBox="0 0 760 434" aria-hidden="true">
      <circle cx="650" cy="200" r="210" fill="var(--white)"/>
      <rect x="650" y="0" width="110" height="434" fill="var(--white)"/>
      <path d="M510 60 A198 198 0 0 0 616 395" fill="none" stroke="var(--ink)" stroke-width="4" stroke-linecap="round"/>
    </svg>
    <div class="brand"><span class="brand-dot"></span>Raven Forge and Mend</div>

    <div class="owner">
      <p class="owner-name">Dalton Whitcomb</p>
      <p class="owner-role">Owner</p>
    </div>

    <ul class="services">
      <li>Fabrication</li>
      <li>Mobile Welding</li>
      <li>Semi Repair</li>
      <li>Pipe Fence</li>
    </ul>

    <div class="contact">
      <p class="contact-row">
        <svg viewBox="0 0 24 24" aria-hidden="true"><path fill="var(--white)" d="M6.6 10.8a15.1 15.1 0 0 0 6.6 6.6l2.2-2.2c.3-.3.7-.4 1-.2 1.1.4 2.3.6 3.6.6.6 0 1 .4 1 1V20c0 .6-.4 1-1 1A17 17 0 0 1 3 4c0-.6.4-1 1-1h3.5c.6 0 1 .4 1 1 0 1.3.2 2.5.6 3.6.1.3 0 .7-.2 1z"/></svg>
        208-417-3826
      </p>
      <p class="contact-row">
        <svg viewBox="0 0 24 24" aria-hidden="true"><path fill="var(--white)" d="M2 5h20v14H2z"/><path d="M2 5l10 8 10-8" fill="none" stroke="var(--blue-mid)" stroke-width="1.8"/></svg>
        ravenforgeandmend@mailbay.net
      </p>
    </div>
  </section>
</main>
</body>
</html>
```